Laser Tattoo Removal Business Cards

We are looking for a professional business card design for a laser tattoo removal business. Ideally looking for a black business card design. The name of the business is Brightline Tattoo Removal. We place our cards at local tattoo shops so we ideally are looking for something trendy/edgy to draw both male and female clientele in.

Target Market(s)

Male/Female ages 18-60

Contact Information for Business Card

black background ideally.. hoping to stay within greys, whites and black

Font styles to use
Serif
Sans Serif

Colors
121212
a9a9a9
5c5c5c
f5f5f5
ffffff
7f7f7f
606060
848484
9d9d9d

Requirements
Must have
• Employee Info:
• Melissa Thornbury
• Chief Executive Offer
• m: 919.537.2846
• w: 919.362.4178
• f: 919.685.3907
• mthornbury@brightlinetattooremoval.example
• Address:
• 4615 Oakmere Pkwy, Suite 210
• Raleigh, NC 27654
• Website:
• www.brightlinetattooremoval.example
Nice to have
• Myabe business name on back or logo on back and employee info on the front

```html
<!DOCTYPE html>
<html lang="en">
<head>
<meta charset="utf-8">
<title>Brightline Tattoo Removal – Business Cards</title>
<link rel="stylesheet" href="https://fonts.googleapis.com/css2?family=Lato:wght@400;700;900&display=swap">
<style>
  :root {
    --ink: #121212;
    --paper: #ffffff;
    --paper-soft: #f5f5f5;
    --grey-dark: #5c5c5c;
    --grey-mid: #7f7f7f;
    --grey-light: #a9a9a9;
    --stage: #2b2b2b;
  }
  * { box-sizing: border-box; margin: 0; padding: 0; }
  html, body {
    width: 1200px; height: 900px; overflow: hidden;
    background: var(--stage);
    font-family: "Lato", sans-serif;
  }
  .canvas {
    position: relative; width: 1200px; height: 900px;
  }
  .card {
    position: absolute; left: 320px; width: 560px; height: 320px;
    border-radius: 14px; overflow: hidden;
    box-shadow: 0 10px 30px rgba(0,0,0,0.45);
  }
  .card--back { top: 95px; background: var(--ink); color: var(--paper); }
  .card--front { top: 485px; background: var(--paper); color: var(--ink); }

  /* Brand wordmark */
  .brand {
    text-align: center; font-weight: 400; text-transform: uppercase;
  }
  .brand__name { display: block; font-size: 50px; letter-spacing: 4px; line-height: 1; }
  .brand__sub {
    display: block; font-size: 19px; letter-spacing: 5px; margin-top: 14px;
  }
  .brand__rule {
    display: flex; align-items: center; justify-content: center; gap: 12px;
  }
  .brand__rule::before, .brand__rule::after {
    content: ""; width: 18px; height: 1px; background: currentColor;
  }

  .card--back .brand { position: absolute; top: 78px; left: 0; right: 0; color: var(--paper); }
  .card--back .website {
    position: absolute; bottom: 52px; left: 0; right: 0; text-align: center;
    font-size: 14px; letter-spacing: 2px; color: var(--paper-soft);
  }

  .card--front .brand {
    position: absolute; top: 34px; right: 40px; color: var(--ink);
  }
  .card--front .brand__name { font-size: 38px; letter-spacing: 3px; }
  .card--front .brand__sub { font-size: 15px; letter-spacing: 4px; margin-top: 10px; }

  /* Ribbons */
  .ribbon {
    position: absolute; background: var(--ink); color: var(--paper);
    display: flex; flex-direction: column; justify-content: center;
  }
  .ribbon--person {
    left: 0; top: 118px; width: 250px; height: 52px; padding-left: 30px;
    clip-path: polygon(0 0, 100% 0, 90% 50%, 100% 100%, 0 100%);
  }
  .ribbon--person .person__name { font-size: 15px; font-weight: 400; }
  .ribbon--person .person__name strong { font-weight: 700; }
  .ribbon--person .person__title { font-size: 11px; color: var(--paper-soft); }

  .ribbon--consult {
    right: 0; top: 142px; width: 210px; height: 52px; padding-right: 22px; text-align: right;
    clip-path: polygon(0 0, 100% 0, 100% 100%, 0 100%, 10% 50%);
  }
  .consult__label { font-size: 11px; font-weight: 700; letter-spacing: 0.5px; }
  .consult__phone { font-size: 21px; font-weight: 900; line-height: 1.05; }

  /* Contact block */
  .contact {
    position: absolute; left: 30px; bottom: 26px; font-size: 12.5px; color: var(--ink);
  }
  .contact__address { font-weight: 700; line-height: 1.35; margin-bottom: 8px; }
  .contact__list { list-style: none; }
  .contact__item { display: flex; align-items: center; gap: 10px; line-height: 1.7; }
  .contact__icon { width: 13px; height: 13px; fill: var(--ink); flex: none; }
</style>
</head>
<body>
<main class="canvas">

  <section class="card card--back" aria-label="Card back">
    <div class="brand">
      <span class="brand__name">Brightline</span>
      <span class="brand__sub brand__rule">Tattoo Removal</span>
    </div>
    <p class="website">www.brightlinetattooremoval.example</p>
  </section>

  <section class="card card--front" aria-label="Card front">
    <div class="brand">
      <span class="brand__name">Brightline</span>
      <span class="brand__sub brand__rule">Tattoo Removal</span>
    </div>

    <div class="ribbon ribbon--person">
      <p class="person__name">Melissa <strong>Thornbury</strong></p>
      <p class="person__title">Chief Executive Offer</p>
    </div>

    <div class="ribbon ribbon--consult">
      <p class="consult__label">FREE CONSULTATION</p>
      <p class="consult__phone">919.362.4178</p>
    </div>

    <div class="contact">
      <p class="contact__address">4615 Oakmere Pkwy, Suite 210<br>Raleigh, NC 27654</p>
      <ul class="contact__list">
        <li class="contact__item">
          <svg class="contact__icon" viewBox="0 0 16 16" aria-hidden="true"><path d="M2 5c0-2 2-3 6-3s6 1 6 3v1h-3V4.5H5V6H2z M4 7h8l2 6H2z"/></svg>
          919.537.2846
        </li>
        <li class="contact__item">
          <svg class="contact__icon" viewBox="0 0 16 16" aria-hidden="true"><path d="M4 1h8v4H4z M1 6h14v6h-3v3H4v-3H1z M5 10v4h6v-4z"/></svg>
          919.685.3907
        </li>
        <li class="contact__item">
          <svg class="contact__icon" viewBox="0 0 16 16" aria-hidden="true"><path d="M1 3h14v10H1z M2 4l6 5 6-5z" fill-rule="evenodd"/></svg>
          mthornbury@brightlinetattooremoval.example
        </li>
      </ul>
    </div>
  </section>

</main>
</body>
</html>
```